Building company buisness cards

We are looking for a sharp modern new look for our business cards.We are a New Zealand based company that specialises in house and land packages.We have attached a photo of the current logo and would like to see if it can be improved somehow if needed.We are open to any colours but we have chosen Black and White at this stage. Feel free to change the font and make the logo smarter looking.Play with the colours and see what looks best.We want a card that looks so good know one will want to throw it away!

Target Market(s)

Building profesonals, home buyers

Industry/Entity Type

Building

Contact Information for Business Card

Garrick Tenwood
0275390628
garrickt@hartvale.co.nz

Font styles to use
Serif
Sans Serif

Colors

Designer to choose colors to be used in the design.

Requirements
Must have
• Just the logo on one side and details on the other
• Clean simple looking card
Nice to have
• Round corners and detail like raised or spot UV
• Something that stands out
Should not have
• To title needed, Director etc

```html
<!DOCTYPE html>
<html lang="en">
<head>
<meta charset="UTF-8">
<title>Hartvale Business Cards</title>
<link rel="stylesheet" href="https://fonts.googleapis.com/css2?family=Crimson+Pro:wght@700&family=Oswald:wght@600&family=Poppins:wght@400&display=swap">
<style>
  :root {
    --backdrop: #ececec;
    --paper: #f7f7f7;
    --ink: #151515;
    --card-black: #1b1b1b;
    --spot-uv: #3c3c3c;
    --muted: #444444;
  }
  * { margin: 0; padding: 0; box-sizing: border-box; }
  html, body {
    width: 1200px; height: 900px; overflow: hidden;
    background: var(--backdrop);
    font-family: "Poppins", sans-serif;
  }
  .canvas {
    position: relative; width: 1200px; height: 900px;
    display: flex; align-items: center; justify-content: center; gap: 40px;
  }
  .card {
    position: relative; width: 540px; height: 310px;
    border-radius: 14px;
    box-shadow: 0 10px 28px rgba(0,0,0,0.18);
  }
  .card--details { background: var(--paper); color: var(--ink); }
  .card--logo { background: var(--card-black); display: flex; align-items: center; justify-content: center; }

  .brand { display: flex; flex-direction: column; align-items: flex-start; }
  .brand__row { display: flex; align-items: center; gap: 12px; }
  .brand__name { font-family: "Crimson Pro", serif; font-weight: 700; font-size: 44px; line-height: 1; letter-spacing: 0.5px; }
  .brand__square { width: 24px; height: 24px; }
  .brand__tagline { font-size: 12px; letter-spacing: 0.6px; margin-top: 6px; }

  .card--details .brand { position: absolute; left: 228px; top: 58px; }
  .card--details .brand__name,
  .card--details .brand__tagline { color: var(--ink); }
  .card--details .brand__square { background: var(--ink); }

  .card--logo .brand__name,
  .card--logo .brand__tagline { color: var(--spot-uv); }
  .card--logo .brand__square { background: var(--spot-uv); }

  .holder-name {
    position: absolute; left: 44px; top: 178px;
    font-family: "Oswald", sans-serif; font-weight: 600; font-size: 19px;
    letter-spacing: 0.5px; text-transform: uppercase;
  }
  .divider { position: absolute; left: 238px; top: 168px; width: 1px; height: 76px; background: var(--ink); }
  .contact { position: absolute; left: 256px; top: 168px; list-style: none; }
  .contact li { display: flex; align-items: center; gap: 9px; font-size: 12.5px; color: var(--muted); height: 25px; }
  .contact svg { width: 12px; height: 12px; flex: none; }
  .contact .icon-fill { fill: var(--ink); }
  .contact .icon-line { fill: none; stroke: var(--ink); stroke-width: 2; }
</style>
</head>
<body>
<main class="canvas">
  <section class="card card--details" aria-label="Card front with contact details">
    <div class="brand">
      <div class="brand__row">
        <span class="brand__name">Hartvale</span>
        <span class="brand__square"></span>
      </div>
      <span class="brand__tagline">Homes shaped around you.</span>
    </div>
    <p class="holder-name">Garrick Tenwood</p>
    <span class="divider"></span>
    <ul class="contact">
      <li>
        <svg viewBox="0 0 24 24" aria-hidden="true"><path class="icon-fill" d="M6.6 10.8a15.1 15.1 0 0 0 6.6 6.6l2.2-2.2c.3-.3.7-.4 1-.2 1.1.4 2.3.6 3.6.6.6 0 1 .4 1 1V20c0 .6-.4 1-1 1A17 17 0 0 1 3 4c0-.6.4-1 1-1h3.5c.6 0 1 .4 1 1 0 1.3.2 2.5.6 3.6.1.3 0 .7-.2 1l-2.3 2.2z"/></svg>
        0275390628
      </li>
      <li>
        <svg viewBox="0 0 24 24" aria-hidden="true"><rect class="icon-line" x="3" y="5" width="18" height="14"/><path class="icon-line" d="M3 6l9 6 9-6"/></svg>
        garrickt@hartvale.co.nz
      </li>
      <li>
        <svg viewBox="0 0 24 24" aria-hidden="true"><circle class="icon-line" cx="12" cy="12" r="9"/><path class="icon-line" d="M3 12h18M12 3c3 3 3 15 0 18M12 3c-3 3-3 15 0 18"/></svg>
        www.hartvale.co.nz
      </li>
    </ul>
  </section>

  <section class="card card--logo" aria-label="Card back with wordmark in spot UV">
    <div class="brand">
      <div class="brand__row">
        <span class="brand__name">Hartvale</span>
        <span class="brand__square"></span>
      </div>
      <span class="brand__tagline">Homes shaped around you.</span>
    </div>
  </section>
</main>
</body>
</html>
```